wine label for a new vineyard

We have developing vineyard which is just starting production. It izs called Amber Hollow Vineyard. It's in rural Australia and the vineyard is on top of a hill where a prominent tree type is pine (technically Calitris). We want a wine label that incorporates these elements (pine trees, hill or ridge). The calitris pines are statuesque in shape, with sillouetes varying from Lombardy pines to Pencil pines. People often chose wines by the label and we are aiming for the upper end of the market so want a label which encourages buyers to believe that this is a sophisticated product. We need to be able to superimpose the grape variety, year and other information so it needs to be uncluttered design.

Target Market(s)

Experienced and discriminating wine drinkers. Prepared to pay $ 20 for a wine they appreciate.

Industry/Entity Type

Product

Requirements
Must have
• Some element of pines and ridge (or hill) so that people associate the name and the label design.
A label which leads the viewer to believe that this is a high quality product.
Nice to have
• We would like to be able to use some elements from the label as a logo.
Should not have
• Jokey wine labels are fashionable but we don't think they suit our segement of the market.

```html
<!DOCTYPE html>
<html lang="en">
<head>
<meta charset="utf-8">
<title>Amber Hollow Vineyard – Wine Labels</title>
<link rel="stylesheet" href="https://fonts.googleapis.com/css2?family=Playfair+Display:wght@400;500;600;700&display=swap">
<style>
  :root {
    --page: #ffffff;
    --paper: #fcfaf2;
    --ink-grey: #85868a;
    --rule: #8c8c8c;
    --merlot: #7b3a40;
    --chardonnay: #86878a;
  }
  html, body {
    margin: 0;
    padding: 0;
    width: 1200px;
    height: 1000px;
    overflow: hidden;
    background: var(--page);
    font-family: "Playfair Display", serif;
  }
  .canvas {
    position: relative;
    width: 1200px;
    height: 1000px;
  }
  .label {
    position: absolute;
    left: 752px;
    width: 360px;
    height: 450px;
    background: var(--paper);
    color: var(--ink-grey);
    transform-origin: top left;
  }
  .label--merlot { top: 35px; --accent: var(--merlot); }
  .label--chardonnay { top: 511px; --accent: var(--chardonnay); }
  .label--small {
    left: 250px;
    top: 487px;
    transform: scale(0.597);
    box-shadow: 0 0 0 1px rgba(0,0,0,0.04);
  }

  .label__spine {
    position: absolute;
    left: 0;
    top: 0;
    width: 93px;
    height: 100%;
    border-right: 1px solid var(--rule);
    box-sizing: border-box;
  }
  .label__name {
    position: absolute;
    inset: 0;
    margin: 0;
    writing-mode: vertical-rl;
    transform: rotate(180deg);
    font-weight: 600;
    font-size: 38px;
    line-height: 93px;
    letter-spacing: -0.3px;
    text-align: start;
    padding: 22px 0;
    box-sizing: border-box;
    white-space: nowrap;
    color: var(--ink-grey);
  }
  .label__details {
    position: absolute;
    left: 324px;
    top: 0;
    width: 24px;
    height: 100%;
    writing-mode: vertical-rl;
    transform: rotate(180deg);
    display: flex;
    justify-content: space-between;
    padding: 24px 0;
    box-sizing: border-box;
    font-size: 13px;
    font-weight: 700;
    letter-spacing: 0.6px;
    line-height: 24px;
    font-variant-numeric: lining-nums;
    color: var(--ink-grey);
  }
  .label__emblem {
    position: absolute;
    left: 176px;
    top: 148px;
    width: 86px;
    height: 128px;
    border-radius: 6px;
    background: var(--accent);
  }
</style>
</head>
<body>
<main class="canvas">
  <section class="label label--chardonnay label--small" aria-label="Chardonnay label, bottle size">
    <div class="label__spine">
      <p class="label__name">amber hollow vineyard</p>
    </div>
    <div class="label__emblem" role="img" aria-label="Grape cluster emblem in grey"></div>
    <div class="label__details">
      <span class="label__variety">chardonnay</span>
      <span class="label__vintage">2013</span>
    </div>
  </section>

  <section class="label label--merlot" aria-label="Merlot label">
    <div class="label__spine">
      <h1 class="label__name">amber hollow vineyard</h1>
    </div>
    <div class="label__emblem" role="img" aria-label="Grape cluster emblem in merlot red"></div>
    <div class="label__details">
      <span class="label__variety">merlot</span>
      <span class="label__vintage">2013</span>
    </div>
  </section>

  <section class="label label--chardonnay" aria-label="Chardonnay label">
    <div class="label__spine">
      <h2 class="label__name">amber hollow vineyard</h2>
    </div>
    <div class="label__emblem" role="img" aria-label="Grape cluster emblem in grey"></div>
    <div class="label__details">
      <span class="label__variety">chardonnay</span>
      <span class="label__vintage">2013</span>
    </div>
  </section>
</main>
</body>
</html>
```